Large online photo magazine needs redesign

We have previously digitised a historical photographic magazine of around 20,000 printed pages and made it available online. The magazine ran up to the early 1970s, and the content is largely black and white photographs of local events, accompanied by short captions.

Although the content is very rich, the design needs to be revisited so that:
* it is visually appealing
* it is responsive (i.e. works in browsers across all manner of devices)
* is faithful to the nature of the content

There are only a few core page types, and the central one is the article page, an example of which can be seen at:
http://snapgazette.example/gisborne/issue/KLR48_19600714/t1-body-d4.html

Any design submitted should be based on the treatment of an article page such as the above.

Given the large number of pages on our site, we need a design which can be templated to work for any content in the collection, i.e. we cannot hand-craft our templates to match a given page of content, rather a template must work acceptably well for all content.

The current site, although basic in design, has the advantage that it is quite efficient in the amount of data per page request (around 100k - 200k). While not adverse to web fonts, banner imagery etc, we will carefully consider the benefit gained from any such treatment against the amount of extra data that needs to be downloaded to the client's browser.

For the right design, we are able ourselves to adapt it to a CSS layout.

An example of each core page type is as follows (though for this project we only expect a design for a single page, as itemised above):

http://snapgazette.example/gisborne/index.html
http://snapgazette.example/gisborne/about.html
http://snapgazette.example/gisborne/help.html
http://snapgazette.example/gisborne/initial/index.html
http://snapgazette.example/gisborne/search/results?type=section&text=smith&cmdSubmit=Go
http://snapgazette.example/gisborne/advanced-search/index.html
http://snapgazette.example/gisborne/issue/KLR48_19600714/t1-front-d1.html
http://snapgazette.example/gisborne/issue/KLR48_19600714/index.html
http://snapgazette.example/gisborne/issue/KLR48_19600714/fig-KLR48_19600714_005a.html
http://snapgazette.example/gisborne/issue/KLR48_19600714/KLR48_19600714_012.html
http://snapgazette.example/gisborne/issue/KLR48_19600714/thumbnails.html

Target Market(s)

A general browsing audience of all ages, but skewed towards the older generations, and those interested in family / regional history.

The average user will not be particularly web-savy, and the treatment of the content should not detract / distract from the actual content itself.

Industry/Entity Type

Events

Requirements
Must have
• * it is visually appealing
The content should be visually appealing to the audience, which can be defined as a general browsing audience of all ages, but skewed towards the middle and older generations.

* it is responsive (the design can be adapted - by us - to work in browsers across all manner of devices)

The magazine covers (http://snapgazette.example/gisborne/issues/index.html) offer some possible inspiration for treatment of the material.

```html
<!DOCTYPE html>
<html lang="en">
<head>
<meta charset="utf-8">
<title>Gisborne Snap Gazette – 14 July 1960</title>
<link href="https://fonts.googleapis.com/css2?family=Open+Sans:wght@300;400;600;700;800&display=swap" rel="stylesheet">
<style>
:root{
  --brand:#c93b4f;
  --panel:#eeeeee;
  --ink:#454545;
  --muted:#777;
  --dark:#3d3d3d;
  --rule:#d6d6d6;
}
*{box-sizing:border-box;margin:0;padding:0}
html,body{width:1009px;height:1200px;overflow:hidden;background:#fff;font-family:"Open Sans",sans-serif;color:var(--ink)}
.masthead{height:52px;background:var(--brand);border-top:1px solid #b0b0b0;display:flex;align-items:center;padding-left:56px}
.masthead-name{color:#fff;font-size:26px;font-weight:700;letter-spacing:.5px}
.utility{height:33px;display:flex;align-items:center;justify-content:space-between;padding:0 137px 0 136px}
.breadcrumb{font-size:8.8px;color:#333}
.search{width:186px;height:20px;border:1px solid #ddd;border-radius:10px;display:flex;align-items:center;padding-left:10px;font-size:7.5px;color:#555;gap:8px}
.navbar{height:16px;background:var(--brand);display:flex;justify-content:space-between;align-items:center;padding:0 138px 0 136px;font-size:8.8px;color:#fff}
.navbar span.sep{margin:0 4px}
.hero{position:absolute;left:136px;top:110px;width:735px;height:106px;background:linear-gradient(180deg,#b9b9b9 0%,#9c9c9c 50%,#5a5a5a 100%)}
.hero-label{position:absolute;left:29px;top:30px;background:#3a3a3a;color:#fff;font-size:16px;padding:5px 12px;letter-spacing:.5px}
.panel{position:absolute;left:136px;top:227px;width:735px;height:913px;background:var(--panel);border-radius:3px}
.article{position:absolute;left:29px;width:677px;height:160px}
.rule{position:absolute;left:29px;width:677px;height:1px;background:var(--rule)}
.photo{position:absolute;left:0;top:0;width:160px;height:160px;box-shadow:0 1px 3px rgba(0,0,0,.35)}
.print{position:absolute;left:664px;width:13px;height:12px}
.body{position:absolute;left:199px;top:9px;width:478px}
.head{display:flex;align-items:center;height:61px}
.date{width:60px;height:61px;background:#fff;box-shadow:0 1px 2px rgba(0,0,0,.25);text-align:center;flex:none;margin-left:-3px}
.date-top{height:12px;background:var(--brand);position:relative}
.date-top::after{content:"";position:absolute;left:26px;top:8px;width:8px;height:1px;background:#fff}
.date-day{font-size:13px;color:#888;margin-top:5px;line-height:16px}
.date-year{font-size:13px;font-weight:700;color:#333;line-height:17px}
.title-block{margin-left:16px}
.title{font-size:19.5px;font-weight:800;color:var(--ink);line-height:24px}
.dek{font-size:7.2px;color:#777;margin-top:2px}
.text{font-size:10.6px;line-height:14.4px;color:var(--ink);margin-top:16px}
.more{display:inline-flex;align-items:center;margin-top:7px;height:22px;background:var(--dark);color:#fff;font-size:9px;border-radius:2px;box-shadow:0 1px 2px rgba(0,0,0,.3)}
.more span{padding:0 7px}
.more i{display:flex;align-items:center;justify-content:center;width:22px;height:22px;border-left:1px solid #555}
.pager{position:absolute;top:878px;width:80px;height:21px;background:#fff;border:1px solid #aaa;box-shadow:0 1px 2px rgba(0,0,0,.25);font-size:11.5px;text-align:center;line-height:19px}
.pager.prev{left:31px;color:var(--brand)}
.pager.next{left:635px;color:#222}
.footer{position:absolute;top:1148px;left:0;width:1009px;text-align:center}
.licence{display:inline-block;width:63px;height:23px;background:#222;border:2px solid #999}
.footer p{font-size:8.8px;color:#444;margin-top:6px}
</style>
</head>
<body>
<header class="masthead"><span class="masthead-name">Gisborne Snap Gazette</span></header>
<div class="utility">
  <div class="breadcrumb">Gisborne Snap Gazette &gt; Issues &gt; KLR48_19600714 &gt; t1-body-d4</div>
  <div class="search"><svg width="7" height="7" viewBox="0 0 10 10"><circle cx="4" cy="4" r="3" fill="none" stroke="#888" stroke-width="1.4"/><line x1="6.3" y1="6.3" x2="9" y2="9" stroke="#888" stroke-width="1.4"/></svg>SEARCH THE SITE</div>
</div>
<nav class="navbar">
  <div>Home<span class="sep">|</span>About<span class="sep">|</span>Browse&nbsp; Gisborne Snap Gazette<span class="sep">|</span>A-Z People</div>
  <div>Advanced search<span class="sep">&nbsp;|&nbsp;</span>Help<span class="sep">&nbsp;|&nbsp;</span>Report an error</div>
</nav>
<div class="hero" role="img" aria-label="Banner photograph of a red umbrella above a crowd of grey umbrellas">
  <div class="hero-label">SNAP GAZETTE</div>
</div>

<main class="panel">
  <article class="article" style="top:30px">
    <svg class="print" style="top:-15px" viewBox="0 0 13 12"><rect x="3" y="0" width="7" height="3" fill="#444"/><rect x="0" y="3" width="13" height="6" rx="1" fill="#444"/><rect x="3" y="7" width="7" height="5" fill="#fff" stroke="#444"/></svg>
    <div class="photo" role="img" aria-label="Black and white photograph of three sisters in air hostess uniforms" style="background:linear-gradient(160deg,#d8d4c8,#6f6b63 55%,#2c2a27)"></div>
    <div class="body">
      <div class="head"><div class="date"><div class="date-top"></div><div class="date-day">July 14</div><div class="date-year">1960</div></div>
        <div class="title-block"><h2 class="title">Flying Sisters from Gisborne</h2><p class="dek">This is probably something of a record--three sisters</p></div></div>
      <p class="text">This is probably something of a record--three sisters who are all air hostesses. They are the Harlow sisters.....Marguerite, Elsa, and Rosalind, daughters of Mr and Mrs W. G. Harlow, Kemble Road, Gisborne.</p>
      <a class="more"><span>CONTINUE READING</span><i><svg width="10" height="7" viewBox="0 0 10 7"><path d="M1 1l4 4 4-4" fill="none" stroke="#fff" stroke-width="1.6"/></svg></i></a>
    </div>
  </article>
  <div class="rule" style="top:212px"></div>

  <article class="article" style="top:233px">
    <svg class="print" style="top:-2px" viewBox="0 0 13 12"><rect x="3" y="0" width="7" height="3" fill="#444"/><rect x="0" y="3" width="13" height="6" rx="1" fill="#444"/><rect x="3" y="7" width="7" height="5" fill="#fff" stroke="#444"/></svg>
    <div class="photo" role="img" aria-label="Black and white photograph of three band members in matching blazers" style="background:linear-gradient(160deg,#e0ddd4,#5a5752 50%,#1f1e1c)"></div>
    <div class="body">
      <div class="head"><div class="date"><div class="date-top"></div><div class="date-day">July 14</div><div class="date-year">1960</div></div>
        <div class="title-block"><h2 class="title">Personal</h2><p class="dek">These are the members of the No. 2 Starlight Show Band,</p></div></div>
      <p class="text" style="margin-top:12px">These are the members of the No. 2 Starlight Show Band, now entertaining at Surfers Paradise, Queensland, The band includes two Gisborne members. From left, Peter Rowe (Rotorua), Henare Tane (Gisborne), Rua Matene (Gisborne), Johnny Brooks (Waikato), Arthur Lyle (North Auckland), and Colin Strand (Invercargill). Their vocalist is Joan Mercer.</p>
      <a class="more"><span>CONTINUE READING</span><i><svg width="10" height="7" viewBox="0 0 10 7"><path d="M1 1l4 4 4-4" fill="none" stroke="#fff" stroke-width="1.6"/></svg></i></a>
    </div>
  </article>
  <div class="rule" style="top:414px"></div>

  <article class="article" style="top:435px">
    <svg class="print" style="top:-2px" viewBox="0 0 13 12"><rect x="3" y="0" width="7" height="3" fill="#444"/><rect x="0" y="3" width="13" height="6" rx="1" fill="#444"/><rect x="3" y="7" width="7" height="5" fill="#fff" stroke="#444"/></svg>
    <div class="photo" role="img" aria-label="Black and white photograph of a stage show with a man on a ladder" style="background:linear-gradient(160deg,#cfc9bc,#a39d90 50%,#3a3835)"></div>
    <div class="body">
      <div class="head"><div class="date"><div class="date-top"></div><div class="date-day">July 14</div><div class="date-year">1960</div></div>
        <div class="title-block" style="margin-left:14px"><h2 class="title">Ray Dunmore in Gisborne</h2><p class="dek">Len Carver got several rungs up the ladder</p></div></div>
      <p class="text">Durable Ray Dunmore, with his pretty wife Phyllis May and his Brightway Soap stage and radio show, came to Gisborne recently and packed the Opera House with patrons, whose admission money, to the tune of £200, will go to the combined Surf Life-Saving Clubs of Gisborne.<br>Pictures taken during the first half of the programme show some of those who matched wits with the irrepressible Ray.</p>
      <a class="more"><span>CONTINUE READING</span><i><svg width="10" height="7" viewBox="0 0 10 7"><path d="M1 1l4 4 4-4" fill="none" stroke="#fff" stroke-width="1.6"/></svg></i></a>
    </div>
  </article>
  <div class="rule" style="top:643px"></div>

  <article class="article" style="top:665px">
    <svg class="print" style="top:-4px" viewBox="0 0 13 12"><rect x="3" y="0" width="7" height="3" fill="#444"/><rect x="0" y="3" width="13" height="6" rx="1" fill="#444"/><rect x="3" y="7" width="7" height="5" fill="#fff" stroke="#444"/></svg>
    <div class="photo" role="img" aria-label="Black and white wedding party photograph with printed caption below" style="background:linear-gradient(180deg,#dcd8ce,#8f8a80 45%,#bdb8ad 80%,#ece9e2)"></div>
    <div class="body">
      <div class="head"><div class="date"><div class="date-top"></div><div class="date-day">July 14</div><div class="date-year">1960</div></div>
        <div class="title-block"><h2 class="title">Wedding Bells</h2><p class="dek">FARLEY--PRENTICE. At St Columba's Church</p></div></div>
      <p class="text">FARLEY--PRENTICE. At St Columba's Church, Marion Ruth, daughter of Mr and Mrs G. T. M. Prentice, 210 Harris Road, to Kenneth Alan, son of Mr and Mrs D. T. Farley, 18 Wilton Street. Mrs Patricia Dunne was matron of honour and Miss Elizabeth Norris the bridesmaid. The junior bridesmaids were Misses Irene Prentice, sister of the bride, and June Falkner, cousin of the bride. Mr Brian Dunne was best man, and Mr Bruce Tilson was groomsman. Future home, Gisborne.</p>
      <a class="more"><span>CONTINUE READING</span><i><svg width="10" height="7" viewBox="0 0 10 7"><path d="M1 1l4 4 4-4" fill="none" stroke="#fff" stroke-width="1.6"/></svg></i></a>
    </div>
  </article>

  <a class="pager prev">PREVIOUS</a>
  <a class="pager next">NEXT</a>
</main>

<footer class="footer">
  <span class="licence"></span>
  <p>2014 Eastland Heritage Library</p>
</footer>
</body>
</html>
```